Coffee Bag Design for Tollbury Coffee

We’re excited to invite you to help us bring Tollbury Coffee to life on grocery store shelves with a design that embodies our mission of spreading goodness and creating a lasting impact. Tollbury Coffee represents warmth, positivity, and the power of small actions to create ripples of goodness. Each cup not only offers a rich, gourmet coffee experience but also gives back to the community, with $2 from each bag supporting local food banks.

To reflect this vision, we’d love for the design to feature a dark (greyish) blue as the base color to convey depth and quality, complemented by a vibrant light blue that will catch the eye and add energy. Tan or gold accents could add an elegant touch and a feeling of warmth. We are aiming for a look that feels uplifting and engaging, with simplicity and elegance, yet stands out amid other brands on the shelf.

I am attaching the dimension of the bag.

Other information that needs to be listed:
Ingredients: 100% Arabica Coffee
Net Wt. 12 oz. (340 g)
Roasted and distributed by:
Name
Address
email

Text on the back of the bag:
Tollbury Coffee is crafted with a belief that kindness and positivity can spread, touching countless lives with every sip. This gourmet blend delivers a rich taste experience while giving back, as $2 from each bag sold is donated to local food banks to help those in need. Enjoy the warmth and goodness in each cup, knowing you’re making a difference with every purchase.

Thank you!

```html
<!DOCTYPE html>
<html lang="en">
<head>
<meta charset="utf-8">
<title>Tollbury Coffee – Costa Rica Bag Front</title>
<link href="https://fonts.googleapis.com/css2?family=Josefin+Sans:wght@300;400&family=Poppins:ital,wght@0,500;0,600;1,400&family=Roboto:wght@400;700;900&display=swap" rel="stylesheet">
<style>
  :root {
    --backdrop: #e4e4e4;
    --navy: #1b2943;
    --navy-deep: #131d31;
    --gold: #c9ae72;
    --gold-light: #e3cd93;
    --sky: #2f8bd0;
    --sky-light: #5cb0ea;
    --cream: #ede4cd;
    --ink: #1d3763;
    --label-blue: #1f4d86;
  }
  * { box-sizing: border-box; margin: 0; padding: 0; }
  html, body { width: 1200px; height: 933px; overflow: hidden; background: var(--backdrop); }
  .canvas { position: relative; width: 1200px; height: 933px; }

  .bag {
    position: absolute; left: 350px; top: 26px; width: 500px; height: 880px;
    border-radius: 14px 14px 4px 4px; overflow: hidden; background: var(--navy);
  }
  .bag__pattern {
    position: absolute; inset: 0;
    background: linear-gradient(135deg, var(--navy) 0%, #2a3650 35%, #574f3f 55%, var(--navy) 80%, #3a3a3c 100%);
  }
  .bag__band {
    position: absolute; top: 0; bottom: 0; left: 150px; width: 200px;
    background: linear-gradient(180deg, var(--sky) 0%, var(--sky-light) 50%, var(--sky) 100%);
  }
  .bag__band::before, .bag__band::after {
    content: ""; position: absolute; top: 0; bottom: 0; width: 14px;
    background: linear-gradient(90deg, var(--gold) 0 4px, transparent 4px 8px, var(--gold-light) 8px 14px);
  }
  .bag__band::before { left: -14px; }
  .bag__band::after { right: -14px; transform: scaleX(-1); }

  .brand-name {
    position: absolute; left: 150px; top: 215px; width: 200px;
    text-align: center; color: var(--navy-deep);
    font-family: "Josefin Sans", sans-serif; font-weight: 400;
    font-size: 36px; line-height: 1.15; letter-spacing: 2px;
  }

  .label {
    position: absolute; left: 65px; top: 472px; width: 325px; height: 240px;
    background: var(--cream); color: var(--ink); padding: 14px 14px 10px;
  }
  .label__head { display: flex; justify-content: space-between; align-items: flex-start; }
  .label__brand { font-family: "Josefin Sans", sans-serif; font-weight: 300; font-size: 26px; line-height: 1; }
  .label__tagline { font-family: "Josefin Sans", sans-serif; font-weight: 400; font-size: 10px; margin: 3px 0 0 68px; }
  .label__seal { width: 50px; height: 50px; border: 1px solid var(--ink); border-radius: 50%; margin-top: -4px; }

  .label__grid {
    display: grid; grid-template-columns: 1fr 1fr; margin-top: 8px;
    border-top: 1px solid var(--ink); border-bottom: 1px solid var(--ink);
  }
  .label__quote {
    font-family: "Poppins", sans-serif; font-style: italic; font-size: 6.4px; line-height: 1.35;
    text-align: right; padding: 6px 6px 6px 0; border-right: 1px solid var(--ink);
  }
  .origin {
    background: var(--label-blue); color: var(--cream); text-align: center;
    font-family: "Roboto", sans-serif; font-weight: 900; padding: 6px 4px; margin: 8px 0 6px 0;
  }
  .origin__country { font-size: 19px; line-height: 1; }
  .origin__farm { font-size: 10px; letter-spacing: .5px; margin-top: 2px; }

  .spec { display: flex; align-items: stretch; border-top: 1px solid var(--ink); min-height: 50px; }
  .spec--notes { border-right: 1px solid var(--ink); }
  .spec__tab {
    width: 14px; background: var(--label-blue); color: var(--cream);
    font-family: "Roboto", sans-serif; font-size: 6.5px; writing-mode: vertical-rl; transform: rotate(180deg);
    text-align: center; letter-spacing: .5px;
  }
  .spec__text { font-family: "Poppins", sans-serif; font-style: italic; font-weight: 600; font-size: 7.5px; padding: 10px 6px; line-height: 1.3; }
  .roast { display: flex; gap: 6px; align-items: center; padding-left: 10px; }
  .roast svg { width: 34px; height: 32px; }

  .label__foot {
    display: grid; grid-template-columns: 1fr 1fr; padding-top: 6px;
    font-family: "Poppins", sans-serif; font-size: 9px;
  }
  .label__foot strong { font-weight: 600; }
  .foot__method { font-weight: 600; font-size: 8px; line-height: 1.15; }
  .foot__right { display: flex; justify-content: space-between; }
  .foot__weight { font-family: "Roboto", sans-serif; font-weight: 700; font-size: 10px; text-align: right; line-height: 1.6; }
</style>
</head>
<body>
<div class="canvas">
  <div class="bag">
    <div class="bag__pattern" role="img" aria-label="Interlocking gold geometric lattice pattern on dark navy"></div>
    <div class="bag__band" role="img" aria-label="Light blue vertical band with fine woven texture"></div>

    <div class="brand-name">Tollbury<br>Coffee</div>

    <div class="label">
      <div class="label__head">
        <div>
          <div class="label__brand">Tollbury Coffee</div>
          <div class="label__tagline">100% Arabica Coffee</div>
        </div>
        <div class="label__seal"></div>
      </div>

      <div class="label__grid">
        <p class="label__quote">“Fruity Aroma,Long Sweet Finish,Structured Acidity,Juicy And Silky Mouthfeel,Flavour Note of Apricot,Caramel,Mixed Berries And Chocolate”</p>
        <div class="origin">
          <div class="origin__country">COSTA RICA</div>
          <div class="origin__farm">HACIENDA VERDELA</div>
        </div>
        <div class="spec spec--notes">
          <div class="spec__tab">NOTES</div>
          <div class="spec__text">Mixed Berries And<br>Chocolate,Caramel</div>
        </div>
        <div class="spec">
          <div class="spec__tab">ROAST</div>
          <div class="roast">
            <svg viewBox="0 0 34 32" fill="none" stroke="#1d3763" stroke-width="2"><path d="M10 2c-2 2 2 3 0 5M15 2c-2 2 2 3 0 5"/><path d="M3 10h22v8a9 9 0 0 1-9 9h-4a9 9 0 0 1-9-9z" fill="#1f4d86"/><path d="M25 13h3a3 3 0 0 1 0 6h-4"/><path d="M2 30h26"/></svg>
            <svg viewBox="0 0 34 32" fill="none" stroke="#1d3763" stroke-width="2"><path d="M10 2c-2 2 2 3 0 5M15 2c-2 2 2 3 0 5"/><path d="M3 10h22v8a9 9 0 0 1-9 9h-4a9 9 0 0 1-9-9z"/><path d="M4 17h20a8 8 0 0 1-8 9h-4a8 8 0 0 1-8-9z" fill="#1f4d86" stroke="none"/><path d="M25 13h3a3 3 0 0 1 0 6h-4"/><path d="M2 30h26"/></svg>
            <svg viewBox="0 0 34 32" fill="none" stroke="#1d3763" stroke-width="2"><path d="M10 2c-2 2 2 3 0 5M15 2c-2 2 2 3 0 5"/><path d="M3 10h22v8a9 9 0 0 1-9 9h-4a9 9 0 0 1-9-9z"/><path d="M5 20c5-3 12 3 18-1"/><path d="M25 13h3a3 3 0 0 1 0 6h-4"/><path d="M2 30h26"/></svg>
          </div>
        </div>
      </div>

      <div class="label__foot">
        <div><strong>Roasted</strong> coffee<br><strong>Whole</strong> bean</div>
        <div class="foot__right">
          <div class="foot__method">Traditional<br>Natural<br>Method</div>
          <div class="foot__weight">Net Wt.<br>12 oz. (340 g)</div>
        </div>
      </div>
    </div>
  </div>
</div>
</body>
</html>
```